Salon and Spa Distributor Business Card

Need a business card. We are are distributor in the salon and spa industry. We identify with natural beauty. Need a card with:
Company Name: Petal Quarry"
Title: "President & CEO"
Address
Company Phone number
email
website
Tag Line:" The Professional Salon Source"

Industry/Entity Type

Business

Contact Information for Business Card

Name: Dov Strommen
Title: "President & CEO"
Address: 31 Harlow Ln, Bexmoor, NJ 07813
Company Phone number: 800-463-5918
email: dovstrommen@petalquarry.example
website: www.petalquarry.example

Requirements
Should not have
• No black backgrounds

```html
<!DOCTYPE html>
<html lang="en">
<head>
<meta charset="utf-8">
<title>Petal Quarry — Business Card</title>
<link href="https://fonts.googleapis.com/css2?family=Mulish:wght@300;400;800&display=swap" rel="stylesheet">
<style>
  :root {
    --stage: #e7e9e6;
    --card-white: #ffffff;
    --brand-green: #3f9e2c;
    --brand-green-deep: #2f7f22;
    --back-green: #3a9233;
    --back-green-dark: #2d7a28;
    --ink-grey: #5d5f5e;
    --soft-grey: #9a9c9b;
    --band-grey: #c9cbca;
  }
  * { box-sizing: border-box; margin: 0; padding: 0; }
  html, body { width: 1200px; height: 974px; overflow: hidden; }
  body {
    background: var(--stage);
    font-family: "Mulish", sans-serif;
    position: relative;
  }
  .card {
    position: absolute;
    left: 280px;
    width: 640px;
    height: 366px;
    border-radius: 22px;
    overflow: hidden;
    box-shadow: 0 8px 24px rgba(0,0,0,0.12);
  }
  .card-front { top: 90px; background: var(--card-white); }
  .card-back { top: 536px; background: var(--back-green); }

  .swoosh { position: absolute; left: 0; top: 0; width: 640px; height: 366px; }

  .brand-block { position: absolute; left: 52px; top: 78px; width: 250px; }
  .brand-lockup { display: flex; align-items: center; gap: 12px; }
  .brand-dot { width: 34px; height: 34px; border-radius: 50%; background: var(--brand-green); flex: none; }
  .brand-name {
    font-weight: 400; font-size: 30px; color: var(--brand-green);
    letter-spacing: -0.3px; white-space: nowrap;
  }
  .tagline {
    margin: 14px 0 0 46px;
    font-weight: 300; font-size: 19px; line-height: 1.3; color: var(--soft-grey);
  }

  .divider {
    position: absolute; left: 318px; top: 84px;
    width: 1px; height: 150px; background: #d8d9d8;
  }

  .contact-block { position: absolute; left: 340px; top: 86px; width: 290px; color: var(--ink-grey); }
  .person-name { font-weight: 800; font-size: 21px; color: var(--brand-green); letter-spacing: 0.4px; text-transform: uppercase; }
  .person-title { font-weight: 400; font-size: 15px; margin-top: 2px; }
  .contact-list { list-style: none; margin-top: 16px; font-size: 14px; line-height: 1.55; }
  .contact-list li { display: flex; align-items: center; gap: 8px; white-space: nowrap; }
  .contact-icon { width: 13px; height: 13px; flex: none; }
  .address { margin-top: 10px; font-size: 14px; line-height: 1.5; }

  .back-pattern {
    position: absolute; inset: 0;
    background: radial-gradient(circle at 40% 40%, #46a23d 0%, var(--back-green) 55%, var(--back-green-dark) 100%);
  }
  .back-name {
    position: absolute; left: 0; right: 0; top: 146px; text-align: center;
    font-weight: 400; font-size: 60px; color: #4fae44; letter-spacing: -0.5px;
  }
</style>
</head>
<body>

  <section class="card card-front" aria-label="Business card front">
    <svg class="swoosh" viewBox="0 0 640 366" aria-hidden="true">
      <path d="M0 226 C 120 250, 260 300, 392 366 L 0 366 Z" fill="var(--band-grey)"/>
      <path d="M0 244 C 120 268, 240 310, 356 366 L 0 366 Z" fill="#ffffff"/>
      <path d="M0 262 C 110 282, 220 320, 318 366 L 0 366 Z" fill="var(--brand-green)"/>
    </svg>

    <div class="brand-block">
      <div class="brand-lockup">
        <span class="brand-dot"></span>
        <span class="brand-name">Petal Quarry</span>
      </div>
      <p class="tagline">The Professional<br>Salon Source</p>
    </div>

    <div class="divider"></div>

    <div class="contact-block">
      <p class="person-name">Dov Strommen</p>
      <p class="person-title">President &amp; CEO</p>
      <ul class="contact-list">
        <li>
          <svg class="contact-icon" viewBox="0 0 16 16"><path d="M3.5 1.5 L6 1 L7.5 4.5 L5.8 5.8 C6.6 7.6 8.4 9.4 10.2 10.2 L11.5 8.5 L15 10 L14.5 12.5 C14.3 13.6 13.3 14.5 12 14.4 C6.5 13.8 2.2 9.5 1.6 4 C1.5 2.7 2.4 1.7 3.5 1.5 Z" fill="var(--brand-green)"/></svg>
          800-463-5918
        </li>
        <li>
          <svg class="contact-icon" viewBox="0 0 16 16"><rect x="1" y="3" width="14" height="10" rx="1" fill="var(--brand-green)"/><path d="M1.5 3.8 L8 9 L14.5 3.8" stroke="#fff" stroke-width="1.4" fill="none"/></svg>
          dovstrommen@petalquarry.example
        </li>
        <li>
          <svg class="contact-icon" viewBox="0 0 16 16"><circle cx="8" cy="8" r="6.5" fill="none" stroke="var(--brand-green)" stroke-width="1.5"/><ellipse cx="8" cy="8" rx="3" ry="6.5" fill="none" stroke="var(--brand-green)" stroke-width="1.2"/><path d="M1.5 8 H14.5 M2.5 5 H13.5 M2.5 11 H13.5" stroke="var(--brand-green)" stroke-width="1.1"/></svg>
          www.petalquarry.example
        </li>
      </ul>
      <p class="address">31 Harlow Ln,<br>Bexmoor, NJ 07813</p>
    </div>
  </section>

  <section class="card card-back" aria-label="Business card back">
    <div class="back-pattern" role="img" aria-label="Repeating spot-UV pattern of the brand symbol in tonal green"></div>
    <p class="back-name">Petal Quarry</p>
  </section>

</body>
</html>
```